Vantiqo custom business card design

Need a authentic, innovative business card design for a new mobile app business. I am uploading a few screen images from our app for you to view. I would like app design theme to match business card design. I can also send logo images.

```html
<!DOCTYPE html>
<html lang="en">
<head>
<meta charset="utf-8">
<title>Vantiqo Business Card</title>
<link rel="stylesheet" href="https://fonts.googleapis.com/css2?family=Lato:wght@400;700;900&family=Arimo:wght@400;700&display=swap">
<style>
  :root {
    --backdrop: #8b5a2f;
    --kraft-light: #ddbd92;
    --kraft-mid: #c99d6c;
    --kraft-dark: #b7885a;
    --ink: #111111;
  }
  * { margin: 0; padding: 0; box-sizing: border-box; }
  html, body {
    width: 1200px;
    height: 900px;
    overflow: hidden;
    background: var(--backdrop);
  }
  .canvas {
    position: relative;
    width: 1200px;
    height: 900px;
  }
  .card {
    position: absolute;
    background: linear-gradient(135deg, var(--kraft-light) 0%, var(--kraft-mid) 45%, var(--kraft-dark) 100%);
    box-shadow: 3px 4px 8px rgba(0, 0, 0, 0.45);
    color: var(--ink);
    text-align: center;
  }
  .card--contact {
    left: 330px; top: 90px;
    width: 555px; height: 343px;
    font-family: "Arimo", Arial, sans-serif;
  }
  .card--brand {
    left: 330px; top: 470px;
    width: 558px; height: 342px;
  }
  .contact-block {
    position: absolute;
    left: 0; right: 0; top: 62px;
  }
  .person-name {
    font-family: "Lato", sans-serif;
    font-weight: 700;
    font-size: 20px;
    letter-spacing: 0.2px;
    line-height: 24px;
  }
  .person-title {
    font-size: 16px;
    line-height: 20px;
  }
  .rule {
    width: 195px;
    height: 1px;
    background: var(--ink);
    margin: 11px auto 12px;
  }
  .contact-list {
    list-style: none;
    font-size: 16px;
    line-height: 20.3px;
  }
  .contact-list b { font-weight: 700; }
  .address {
    font-size: 16px;
    line-height: 20px;
    margin-top: 17px;
  }
  .brand-mark {
    position: absolute;
    left: 204px; top: 62px;
    width: 150px; height: 150px;
    border-radius: 50%;
    background: var(--ink);
  }
  .brand-name {
    position: absolute;
    left: 0; right: 0; top: 228px;
    font-family: "Lato", sans-serif;
    font-weight: 900;
    font-size: 50px;
    line-height: 56px;
    letter-spacing: 0.5px;
  }
</style>
</head>
<body>
<main class="canvas">
  <section class="card card--contact">
    <div class="contact-block">
      <h1 class="person-name">DANIEL HARTLEY</h1>
      <p class="person-title">Managing Director</p>
      <div class="rule"></div>
      <ul class="contact-list">
        <li><b>P:</b> 044-123 456 789</li>
        <li><b>M:</b> 044-123 456 789</li>
        <li><b>E:</b> info@vantiqo.com</li>
        <li><b>W:</b> www.vantiqo.com</li>
      </ul>
      <div class="rule"></div>
      <p class="address">12345, Address Goes Here<br>Country Name, 123456.</p>
    </div>
  </section>

  <section class="card card--brand">
    <div class="brand-mark"></div>
    <p class="brand-name">Vantiqo</p>
  </section>
</main>
</body>
</html>
```